Business card design for my company.
I would like the card's background colour to be black. You can also see our web site to get an idea of our brand. https://www.tmwhomecrafting.com.au/
- Name
- Email

```html
<!DOCTYPE html>
<html lang="en">
<head>
<meta charset="utf-8">
<title>TMW Home Crafting – Business Card</title>
<link rel="stylesheet" href="https://fonts.googleapis.com/css2?family=Montserrat:wght@400;500;700&display=swap">
<style>
  :root {
    --stage: #2a2a2a;
    --card-black: #141414;
    --brand-green: #0c9a4a;
    --green-deep: #07853f;
    --green-shade: #067035;
    --text-light: #f2f2f2;
    --text-soft: #d6d6d6;
  }
  * { box-sizing: border-box; margin: 0; padding: 0; }
  html, body { width: 1200px; height: 900px; overflow: hidden; }
  body {
    background: var(--stage);
    font-family: "Montserrat", sans-serif;
    display: flex;
    flex-direction: column;
    align-items: center;
    justify-content: center;
    gap: 60px;
  }
  .card {
    width: 560px;
    height: 320px;
    border-radius: 22px;
    position: relative;
    overflow: hidden;
  }
  .card-front {
    background: var(--card-black);
    display: flex;
    align-items: center;
    padding: 0 36px;
  }
  .brand-block {
    width: 228px;
    display: flex;
    flex-direction: column;
    align-items: flex-start;
    gap: 4px;
  }
  .brand-name {
    color: var(--text-light);
    font-weight: 700;
    font-size: 34px;
    line-height: 1.05;
    letter-spacing: 1px;
  }
  .brand-sub {
    color: var(--text-light);
    font-weight: 700;
    font-size: 15px;
    letter-spacing: 4px;
  }
  .divider {
    width: 1.5px;
    height: 190px;
    background: var(--brand-green);
    margin: 0 22px 0 8px;
  }
  .contact-block { display: flex; flex-direction: column; }
  .person-name {
    color: var(--brand-green);
    font-weight: 700;
    font-size: 25px;
    line-height: 1.1;
  }
  .person-title {
    color: var(--text-soft);
    font-size: 13px;
    margin-top: 4px;
  }
  .location {
    color: var(--text-soft);
    font-size: 13px;
    margin-top: 14px;
    margin-bottom: 10px;
  }
  .contact-list { list-style: none; display: flex; flex-direction: column; gap: 6px; }
  .contact-item {
    display: flex;
    align-items: center;
    gap: 8px;
    color: var(--text-light);
    font-size: 12.5px;
  }
  .contact-icon { width: 12px; height: 12px; flex: none; }
  .card-back {
    background: linear-gradient(135deg, var(--brand-green), var(--green-deep));
    display: flex;
    flex-direction: column;
    align-items: center;
    justify-content: center;
    gap: 6px;
  }
  .back-name {
    color: var(--green-shade);
    font-weight: 700;
    font-size: 64px;
    letter-spacing: 2px;
    line-height: 1;
  }
  .back-sub {
    color: var(--green-shade);
    font-weight: 700;
    font-size: 22px;
    letter-spacing: 6px;
  }
</style>
</head>
<body>
  <section class="card card-front">
    <div class="brand-block">
      <span class="brand-name">TMW</span>
      <span class="brand-sub">HOME CRAFTING</span>
    </div>
    <div class="divider"></div>
    <div class="contact-block">
      <h1 class="person-name">Liam Harcourt</h1>
      <p class="person-title">General Manager</p>
      <p class="location">Hobart, Tasmania, Australia</p>
      <ul class="contact-list">
        <li class="contact-item">
          <svg class="contact-icon" viewBox="0 0 24 24"><path fill="#0c9a4a" d="M6.6 10.8a15.1 15.1 0 0 0 6.6 6.6l2.2-2.2c.3-.3.7-.4 1-.2 1.1.4 2.3.6 3.6.6.6 0 1 .4 1 1V20c0 .6-.4 1-1 1A17 17 0 0 1 3 4c0-.6.4-1 1-1h3.5c.6 0 1 .4 1 1 0 1.3.2 2.5.6 3.6.1.3 0 .7-.2 1z"/></svg>
          0400 512 738
        </li>
        <li class="contact-item">
          <svg class="contact-icon" viewBox="0 0 24 24"><rect x="2" y="5" width="20" height="14" rx="1.5" fill="#0c9a4a"/><path d="M3 6l9 7 9-7" fill="none" stroke="#141414" stroke-width="2"/></svg>
          info@tmwhomecrafting.com.au
        </li>
        <li class="contact-item">
          <svg class="contact-icon" viewBox="0 0 24 24"><circle cx="12" cy="12" r="9.5" fill="none" stroke="#0c9a4a" stroke-width="2"/><path d="M2.5 12h19M12 2.5c3 3 3 16 0 19M12 2.5c-3 3-3 16 0 19" fill="none" stroke="#0c9a4a" stroke-width="1.6"/></svg>
          www.tmwhomecrafting.com.au
        </li>
      </ul>
    </div>
  </section>

  <section class="card card-back">
    <span class="back-name">TMW</span>
    <span class="back-sub">HOME CRAFTING</span>
  </section>
</body>
</html>
```